Dental Business Card Design w/logo

Classic, elegant w/a touch of contemporary
Upscale dental facility located in Modesto CA
Specializing in restorative & general dentistry
Providing exceptional customer service to the community
Updates

I prefer script and not bold writing
If you can use the phone; fax and email icons instead of spelling them out, it would be great
No bold colors
Classy and elegant
In the back of the card I would like to see something like this
Your Next Appointment:
Mon     Tue    Wed    Thur (a box next to each of them for marking)
Date:_______________ at_____________ AM    PM  (a box next to them for marking)

Thank you

Target Market(s)

Well established professional

Industry/Entity Type

Dental

Contact Information for Business Card

Velarina Tossudi DMD
4176 Marlow Rd
Suite K7
Modesto, CA 95418

Office: 209-731-5920
Fax: 209-731-8047
Email: tossudidmd@quillmail.example

Requirements
Must have
• Unique classic logo
An easily repeatable design that can be used on letterhead and envelopes
Nice to have
• My initials incorporated into unique design
Should not have
• No cartoons or cheesy themes. This is a practice for the well established and professional individual.

```html
<!DOCTYPE html>
<html lang="en">
<head>
<meta charset="utf-8">
<title>Velarina Tossudi DMD – Business Card</title>
<link rel="stylesheet" href="https://fonts.googleapis.com/css2?family=Roboto+Condensed:wght@700&family=Jost:wght@400&display=swap">
<style>
  :root {
    --page: #ffffff;
    --card-edge: #222222;
    --brand-blue: #0a24e0;
    --brand-gold: #b8960a;
    --ink: #111111;
  }
  html, body {
    margin: 0;
    padding: 0;
    width: 1200px;
    height: 900px;
    overflow: hidden;
    background: var(--page);
  }
  .canvas {
    position: relative;
    width: 1200px;
    height: 900px;
  }
  .business-card {
    position: absolute;
    left: 121px;
    top: 167px;
    width: 964px;
    height: 570px;
    border: 1px solid var(--card-edge);
    box-sizing: border-box;
    background: var(--page);
  }

  /* Practice lockup: one colour, one weight, with a plain circle beside it */
  .brand-mark {
    position: absolute;
    left: 42px;
    top: 274px;
    width: 56px;
    height: 56px;
    border-radius: 50%;
    background: var(--brand-gold);
  }
  .brand-name {
    position: absolute;
    left: 49px;
    top: 225px;
    width: 300px;
    margin: 0;
    font-family: "Roboto Condensed", "Arial Narrow", sans-serif;
    font-weight: 700;
    color: var(--brand-blue);
    text-align: right;
  }
  .brand-name span { display: block; }
  .brand-name .first { font-size: 52px; line-height: 52px; }
  .brand-name .last { font-size: 62px; line-height: 60px; }
  .brand-name .practice { font-size: 36px; line-height: 40px; }

  .details {
    position: absolute;
    right: 49px;
    top: 104px;
    text-align: right;
  }
  .doctor-name {
    margin: 0;
    font-family: "Roboto Condensed", "Arial Narrow", sans-serif;
    font-weight: 700;
    font-size: 52px;
    line-height: 47px;
    color: var(--brand-blue);
  }
  .credential {
    font-family: "Jost", sans-serif;
    font-size: 26px;
    line-height: 30px;
    color: var(--brand-gold);
  }
  .address {
    margin: 50px 0 0;
    font-family: "Jost", sans-serif;
    font-style: normal;
    font-size: 25px;
    line-height: 31px;
    color: var(--ink);
  }
  .contact {
    margin: 28px 0 0;
    padding: 0;
    list-style: none;
    font-family: "Jost", sans-serif;
    color: var(--ink);
  }
  .contact li { line-height: 34px; }
  .contact .label { font-size: 23px; }
  .contact .value { font-size: 28px; }
  .contact .email .value { font-size: 23px; }
</style>
</head>
<body>
<main class="canvas">
  <section class="business-card" aria-label="Business card">
    <span class="brand-mark" aria-hidden="true"></span>
    <h2 class="brand-name">
      <span class="first">VELARINA</span>
      <span class="last">TOSSUDI</span>
      <span class="practice">DENTISTRY</span>
    </h2>

    <div class="details">
      <h1 class="doctor-name">VELARINA<br>TOSSUDI</h1>
      <div class="credential">DMD</div>
      <address class="address">
        4176 Marlow Rd Suite K7<br>
        Modesto, CA 95418
      </address>
      <ul class="contact">
        <li class="office"><span class="label">OFFICE: </span><span class="value">209-731-5920</span></li>
        <li class="fax"><span class="label">FAX: </span><span class="value">209-731-8047</span></li>
        <li class="email"><span class="label">EMAIL: </span><span class="value">tossudidmd@quillmail.example</span></li>
      </ul>
    </div>
  </section>
</main>
</body>
</html>
```